Keystonery Billboard - Financial Services Company (Investments, Tax Planning and Insurance)

Our new office has a billboard directly above the office building. We'd like something eye-catching with a strong Call to Action, with the main part of the billboard being under 7 words if possible. We'd like you to include a way to get ahold of us (either our website keystoneryllc.example or our phone number 302-418-2907. You may also include in small font something to indicate that we've been serving the area since 1980 (the DE area, the tri-state area, the Marlowe Hollow, etc.)

We offer financial planning, tax planning, and insurance, and we help our clients to focus on their goals and happiness by providing everything they need for lifelong wealth under one roof.

Our logos are attached, we use a triangle logo with green and gray. We use the tagline "discover lasting prosperity" but this does not need to be included.

Potential ideas we have seen from other financial companies-
- the concept that the driver spends more time looking at billboards than planning for their retirement
-something along the lines of "everything you need for your finances is in this building right here" planning, investments, taxes, insurance"
-don't spend your time worrying about retirement, let us help you plan for it
-are you working for your money, or is it working for you?
- retirement takes planning, we're here to help
- ready to retire? talk to us
- need investment advice?
- need help investing?
- crossing your fingers isn't a retirement plan. we can help.
- retiring soon? you need help.

Those are just general ideas, please feel free to be creative.

brand colors:
#00b585
#00b185
#000000
#ffffff
#6d6f75
#6d6f75
#6f7074
#021712
#052e24

```html
<!DOCTYPE html>
<html lang="en">
<head>
<meta charset="utf-8">
<title>Keystonery Billboard</title>
<link rel="stylesheet" href="https://fonts.googleapis.com/css2?family=Montserrat:wght@600;700;800&family=Tinos:wght@700&display=swap">
<style>
  :root {
    --brand-green: #00b185;
    --deep-green: #003d29;
    --band-green: #064a33;
    --mid-green: #008a55;
    --light-green: #6ef2a4;
    --brand-grey: #6d6f75;
    --strip-grey: #f1f1f1;
    --white: #ffffff;
    --page: #e4e4e4;
  }
  html, body {
    margin: 0;
    width: 1000px;
    height: 1200px;
    overflow: hidden;
    background: var(--page);
  }
  .canvas {
    position: relative;
    width: 1000px;
    height: 1200px;
  }
  .billboard {
    position: absolute;
    left: 30px;
    top: 366px;
    width: 940px;
    height: 468px;
    box-shadow: 0 14px 30px rgba(0,0,0,0.35);
    background: var(--white);
  }
  .billboard svg { display: block; width: 100%; height: 100%; }
  .headline { font-family: "Montserrat", sans-serif; font-weight: 800; fill: var(--white); }
  .subline { font-family: "Montserrat", sans-serif; font-weight: 700; fill: var(--white); }
  .located { font-family: "Montserrat", sans-serif; font-weight: 700; fill: var(--white); }
  .services { font-family: "Tinos", serif; font-weight: 700; fill: var(--brand-grey); }
  .divider { stroke: var(--brand-green); stroke-width: 3; }
  .contact { font-family: "Montserrat", sans-serif; font-weight: 700; fill: var(--white); }
  .brand-name { font-family: "Montserrat", sans-serif; font-weight: 700; fill: var(--band-green); }
</style>
</head>
<body>
<main class="canvas">
  <section class="billboard" aria-label="Keystonery billboard">
    <svg viewBox="0 0 1330 662" xmlns="http://www.w3.org/2000/svg">
      <defs>
        <linearGradient id="hero-gradient" x1="0" y1="0" x2="1" y2="0">
          <stop offset="0" stop-color="var(--deep-green)"/>
          <stop offset="0.3" stop-color="#0a5a3a"/>
          <stop offset="0.65" stop-color="#2fa66a"/>
          <stop offset="1" stop-color="var(--light-green)"/>
        </linearGradient>
      </defs>

      <!-- hero area -->
      <rect class="hero" x="0" y="14" width="1330" height="446" fill="url(#hero-gradient)"/>
      <!-- brand corner -->
      <polygon class="brand-corner" points="845,14 1330,14 1330,136 900,136" fill="var(--white)"/>
      <text class="brand-name" x="1279" y="92" font-size="50" text-anchor="end">Keystonery</text>

      <!-- location arrow -->
      <polygon class="location-arrow" points="1034,136 1274,136 1240,347 1297,347 1156,447 1012,347 1072,347"
               fill="var(--mid-green)" stroke="#005a38" stroke-width="6" stroke-linejoin="round"/>
      <text class="located" x="1156" y="194" font-size="35" text-anchor="middle">LOCATED</text>
      <text class="located" x="1156" y="239" font-size="35" text-anchor="middle">HERE</text>
      <g class="chevrons" fill="none" stroke="var(--white)" stroke-width="13" stroke-linejoin="miter">
        <polyline points="1126,268 1156,288 1186,268"/>
        <polyline points="1126,298 1156,318 1186,298"/>
        <polyline points="1126,328 1156,348 1186,328"/>
        <polyline points="1126,358 1156,378 1186,358"/>
      </g>

      <!-- headline -->
      <text class="headline" x="62" y="127" font-size="110" textLength="615" lengthAdjust="spacingAndGlyphs">WORRYING</text>
      <text class="headline" x="62" y="237" font-size="110" textLength="727" lengthAdjust="spacingAndGlyphs">ABOUT YOUR</text>
      <text class="headline" x="60" y="347" font-size="110" textLength="934" lengthAdjust="spacingAndGlyphs">MONEY? US TOO!</text>
      <text class="subline" x="62" y="427" font-size="50" textLength="928" lengthAdjust="spacingAndGlyphs">No worry for a free consultation</text>

      <!-- services strip -->
      <rect class="services-strip" x="0" y="460" width="1330" height="106" fill="var(--strip-grey)"/>
      <text class="services" x="60" y="530" font-size="60">Planning</text>
      <line class="divider" x1="338" y1="496" x2="338" y2="532"/>
      <text class="services" x="370" y="535" font-size="60">Investments</text>
      <line class="divider" x1="733" y1="496" x2="733" y2="532"/>
      <text class="services" x="764" y="535" font-size="60">Taxes</text>
      <line class="divider" x1="956" y1="496" x2="956" y2="532"/>
      <text class="services" x="987" y="535" font-size="60">Insurance</text>

      <!-- contact band -->
      <rect class="contact-band" x="0" y="566" width="1330" height="96" fill="var(--band-green)"/>
      <g class="phone-icon">
        <circle cx="89" cy="616" r="28" fill="var(--white)"/>
        <path d="M78 600 l8 -3 l6 11 l-5 5 q4 8 11 12 l5 -5 l11 6 l-3 8 q-4 5 -12 3 q-20 -7 -26 -28 q-1 -7 5 -9 z" fill="var(--band-green)"/>
      </g>
      <text class="contact" x="128" y="637" font-size="60" textLength="440" lengthAdjust="spacingAndGlyphs">302-418-2907</text>
      <line x1="593" y1="597" x2="593" y2="640" stroke="var(--white)" stroke-width="3"/>
      <g class="web-icon" fill="none" stroke="var(--band-green)" stroke-width="2.5">
        <circle cx="652" cy="616" r="28" fill="var(--white)" stroke="none"/>
        <circle cx="652" cy="616" r="17"/>
        <ellipse cx="652" cy="616" rx="7" ry="17"/>
        <line x1="635" y1="616" x2="669" y2="616"/>
        <line x1="638" y1="607" x2="666" y2="607"/>
        <line x1="638" y1="625" x2="666" y2="625"/>
      </g>
      <text class="contact" x="695" y="637" font-size="54" textLength="585" lengthAdjust="spacingAndGlyphs">keystoneryllc.example</text>
    </svg>
  </section>
</main>
</body>
</html>
```